Hollow Thicket, a 3d voxel survival video game needs a card for gaming conventions

I am the lead developer for Hollow Thicket http://www.HollowThicket.example and need a business card to hand out at an indie gaming convention
The card would need to include the game name, website url, my name, position (Lead Developer), e-mail and phone number
The game is a 3d, voxel (with smooth terrain) based survival game with guns and wildlife. The main icon of the game would likely be a grizzly bear but I am willing to accept other designs too.
Attached is a media kit for the game with some images you can use but don't have to its just what little art I can provide. Anything on the website or from the video game can also be used. unrelated art can also be used.
Target Market(s)
Indie Developers/publishers at conferences
Industry/Entity Type
Games
Contact Information for Business Card
Name: Corin Waldrick
Position: Lead Developer
E-mail: Pale_Kettle@mailbox.example
Phone number: 555-372-1186

```html
<!DOCTYPE html>
<html lang="en">
<head>
<meta charset="utf-8">
<title>Hollow Thicket — Business Card</title>
<link rel="stylesheet" href="https://fonts.googleapis.com/css2?family=Source+Sans+3:wght@400;600;800&display=swap">
<style>
  :root {
    --stage-top: #959595;
    --stage-bottom: #717171;
    --card-front: #f3f3f3;
    --brand-red: #9b2716;
    --name-red: #8c2a12;
    --ink: #333333;
    --fur-light: #a0703f;
    --fur-mid: #6b4226;
    --fur-dark: #3f2514;
    --back-glow: #e8dbb9;
    --back-mid: #9a8d62;
    --back-edge: #34300f;
  }
  * { box-sizing: border-box; margin: 0; padding: 0; }
  html, body { width: 1200px; height: 900px; overflow: hidden; }
  body {
    background: linear-gradient(180deg, var(--stage-top), var(--stage-bottom));
    font-family: "Source Sans 3", "Myriad Pro", Arial, sans-serif;
    position: relative;
  }
  .card {
    position: absolute;
    top: 184px;
    height: 491px;
    border-radius: 14px;
    overflow: hidden;
  }
  .card--front { left: 299px; width: 301px; background: var(--card-front); }
  .card--back {
    left: 645px; width: 305px;
    background: radial-gradient(ellipse 70% 62% at 52% 50%, var(--back-glow) 0%, var(--back-mid) 55%, var(--back-edge) 100%);
  }
  .wordmark {
    position: absolute;
    left: 0; right: 0;
    text-align: center;
    color: var(--brand-red);
    font-weight: 800;
    font-size: 40px;
    line-height: 40px;
    letter-spacing: 1px;
    text-transform: uppercase;
  }
  .card--front .wordmark { top: 58px; }
  .card--back .wordmark { top: 204px; }
  .contact {
    position: absolute;
    left: 0; right: 0;
    text-align: center;
    color: var(--ink);
    font-size: 14px;
    line-height: 18px;
  }
  .contact__name { top: 202px; color: var(--name-red); font-weight: 600; font-size: 17px; line-height: 20px; }
  .contact__role { top: 220px; }
  .contact__details { top: 265px; }
  .mascot {
    position: absolute;
    left: 70px; top: 322px;
    width: 231px; height: 169px;
    background:
      radial-gradient(ellipse 28% 30% at 22% 34%, var(--fur-mid) 0%, rgba(107,66,38,0.6) 55%, rgba(107,66,38,0) 100%),
      radial-gradient(ellipse 72% 92% at 78% 80%, var(--fur-light) 0%, var(--fur-mid) 40%, var(--fur-dark) 62%, rgba(63,37,20,0) 82%);
  }
</style>
</head>
<body>
  <section class="card card--front">
    <h1 class="wordmark">Hollow<br>Thicket</h1>
    <p class="contact contact__name">Corin Waldrick</p>
    <p class="contact contact__role">Lead Developer</p>
    <p class="contact contact__details">555-372-1186<br>Pale_Kettle@mailbox.example<br>www.HollowThicket.example</p>
    <div class="mascot" role="img" aria-label="Photograph of a roaring grizzly bear"></div>
  </section>
  <section class="card card--back">
    <p class="wordmark">Hollow<br>Thicket</p>
  </section>
</body>
</html>
```